Local fast-growing company in the service sector

We are looking for a modern business card design, which should also appear on our letterheads

Target Market(s)

Private and industrial sectors

Contact Information for Business Card

Vorname Name
Kellberger Str. 18
71398 Talheimsfeld
Tel.: 07146-839214-0
Name@agentur-kvtl.de

Colors
9d9d9d
919191
aaaaaa

Requirements
Must have
• The logo (file) in silver

```html
<!DOCTYPE html>
<html lang="de">
<head>
<meta charset="utf-8">
<title>KVTL Visitenkarte</title>
<link rel="stylesheet" href="https://fonts.googleapis.com/css2?family=Montserrat:wght@400;600;800&family=Michroma&display=swap">
<style>
  :root {
    --backdrop: #5c5c5e;
    --card-dark: #242426;
    --card-mid: #333336;
    --silver: #aaaaaa;
    --silver-mid: #9d9d9d;
    --silver-dark: #919191;
    --white: #f4f4f4;
  }
  * { margin: 0; padding: 0; box-sizing: border-box; }
  html, body { width: 799px; height: 1200px; overflow: hidden; }
  body {
    background: var(--backdrop);
    font-family: "Montserrat", sans-serif;
    position: relative;
  }
  .card {
    position: absolute;
    left: 80px;
    width: 640px;
    height: 390px;
    background: radial-gradient(ellipse at 55% 55%, var(--card-mid), var(--card-dark) 80%);
    box-shadow: 0 10px 30px rgba(0,0,0,0.45);
  }
  .card--front { top: 130px; }
  .card--back { top: 680px; }

  .brand { display: flex; flex-direction: column; align-items: flex-start; }
  .brand__row { display: flex; align-items: center; gap: 14px; }
  .brand__square { background: var(--silver); }
  .brand__name {
    font-weight: 800;
    color: var(--silver);
    line-height: 1;
    letter-spacing: 1px;
  }
  .brand__web {
    color: var(--silver-mid);
    font-weight: 400;
    letter-spacing: 1px;
  }

  .card--front .brand {
    position: absolute;
    left: 150px;
    top: 120px;
  }
  .card--front .brand__square { width: 62px; height: 62px; }
  .card--front .brand__name { font-size: 92px; }
  .card--front .brand__web { font-size: 31px; margin-left: 76px; margin-top: 4px; }

  .card--back .brand {
    position: absolute;
    left: 50px;
    top: 110px;
  }
  .card--back .brand__square { width: 38px; height: 38px; }
  .card--back .brand__name { font-size: 56px; }
  .card--back .brand__web { font-size: 19px; margin-left: 52px; margin-top: 2px; }

  .contact {
    position: absolute;
    left: 340px;
    top: 190px;
    color: var(--white);
  }
  .contact__name {
    font-family: "Michroma", sans-serif;
    font-size: 19px;
    letter-spacing: 2px;
    margin-bottom: 12px;
  }
  .contact__line {
    font-size: 15px;
    line-height: 22px;
    display: flex;
    align-items: center;
    gap: 8px;
  }
  .contact__icon { width: 14px; height: 14px; fill: var(--white); flex: none; }
</style>
</head>
<body>
  <section class="card card--front">
    <div class="brand">
      <div class="brand__row">
        <span class="brand__square"></span>
        <span class="brand__name">KVTL</span>
      </div>
      <span class="brand__web">agentur-kvtl.de</span>
    </div>
  </section>

  <section class="card card--back">
    <div class="brand">
      <div class="brand__row">
        <span class="brand__square"></span>
        <span class="brand__name">KVTL</span>
      </div>
      <span class="brand__web">agentur-kvtl.de</span>
    </div>

    <div class="contact">
      <p class="contact__name">VORNAME NAME</p>
      <p class="contact__line">Kellberger Str. 18</p>
      <p class="contact__line">71398 Talheimsfeld</p>
      <p class="contact__line">
        <svg class="contact__icon" viewBox="0 0 16 16" aria-hidden="true">
          <path d="M3 1h3l1.5 4-2 1.3a9 9 0 0 0 4.2 4.2L11 8.5l4 1.5v3a2 2 0 0 1-2 2A13 13 0 0 1 1 3a2 2 0 0 1 2-2z"/>
        </svg>
        07146-839214-0
      </p>
      <p class="contact__line">
        <svg class="contact__icon" viewBox="0 0 16 16" aria-hidden="true">
          <path d="M1 3h14v10H1z M2 4l6 5 6-5" fill="none" stroke="#f4f4f4" stroke-width="1.5"/>
        </svg>
        name@agentur-kvtl.de
      </p>
    </div>
  </section>
</body>
</html>
```